4th Generation Family Business Needs a New Card Design!

We are a family owned 4th Generation company. We are based in the Sydney, Australia area and we are desperately in need of a more modern and classy card. We are monumental masons who design, supply & erect lasting memorials throughout cemeteries in Sydney. Our customers are normally in a period of grieving. I have attached logo files that will need to be implemented on the card. Company was established 1935. Australian Owned and Operated. Card needs to be designed to PIXO.com specification.

Target Market(s)

Our target market is based upon people that a grieving for family members that have passed away. We also deal with alot of companies that own and operate cemeteries.

Industry/Entity Type

Business

Contact Information for Business Card

Simon Harcourt, Operations Manager, 0417293086, simon@harcourtmemorials.com.au
Lewis Harcourt, Director, 0491630572, lewis@harcourtmemorials.com.au
Phone # 02 9561 3048
Website: www.harcourtmemorials.com.au
Address: Suite 17, 8 Palfrey Lane, West Carlow, Sydney NSW 2156

Font styles to use
Serif
Decorative
Script

Requirements
Must have
• Would like to see the logo nicely implemented with a modern design. Embossed lettering would be a nice additive.

```html
<!DOCTYPE html>
<html lang="en">
<head>
<meta charset="utf-8">
<title>Harcourt Memorials – Business Card</title>
<link href="https://fonts.googleapis.com/css2?family=Cinzel:wght@400;700&family=Source+Sans+3:wght@400&display=swap" rel="stylesheet">
<style>
  :root {
    --stage-top: #2b2b2b;
    --stage-bottom: #050505;
    --card-light: #ffffff;
    --card-dark: #232122;
    --ink: #111111;
    --paper-text: #f2f2f2;
    --gold: #e8b92c;
  }
  * { margin: 0; padding: 0; box-sizing: border-box; }
  html, body { width: 1200px; height: 900px; overflow: hidden; }
  body {
    position: relative;
    background: linear-gradient(to bottom, var(--stage-top) 0%, #181818 55%, var(--stage-bottom) 100%);
    font-family: "Source Sans 3", "Myriad Pro", Arial, sans-serif;
  }
  .card {
    position: absolute;
    top: 206px;
    width: 275px;
    height: 446px;
    text-align: center;
  }
  .card--front { left: 315px; background: var(--card-light); color: var(--ink); }
  .card--back {
    left: 635px;
    background: radial-gradient(circle at 60% 30%, #2a2829 0%, var(--card-dark) 70%);
    color: var(--paper-text);
  }
  .wordmark {
    font-family: "Cinzel", "Times New Roman", serif;
    font-weight: 400;
    letter-spacing: 1px;
    line-height: 1.05;
  }
  .card--front .wordmark {
    position: absolute; top: 44px; left: 0; right: 0;
    font-size: 28px; color: var(--ink);
  }
  .contact {
    position: absolute; left: 0; right: 0;
    font-size: 12.5px; line-height: 16.5px;
  }
  .contact--simon { top: 138px; }
  .contact--lewis { top: 252px; }
  .contact__name {
    font-family: "Cinzel", "Times New Roman", serif;
    font-weight: 700;
    font-size: 15px;
    letter-spacing: 0.5px;
    line-height: 18px;
  }
  .divider {
    position: absolute; top: 344px; left: 12px; right: 13px;
    border-top: 1.5px solid var(--ink);
  }
  .office {
    position: absolute; top: 374px; left: 0; right: 0;
    font-size: 12.5px; line-height: 16px;
  }
  .brand-square {
    position: absolute; top: 140px; left: 100px;
    width: 75px; height: 75px;
    border: 3px solid var(--gold);
  }
  .card--back .wordmark {
    position: absolute; top: 248px; left: 0; right: 0;
    font-size: 30px; color: var(--paper-text);
  }
  .address {
    position: absolute; top: 353px; left: 0; right: 0;
    font-size: 12.5px; line-height: 16px;
  }
</style>
</head>
<body>
  <section class="card card--front">
    <div class="wordmark">Harcourt<br>Memorials</div>

    <div class="contact contact--simon">
      <div class="contact__name">Simon Harcourt</div>
      <div>Operations Manager</div>
      <div>0417293086</div>
      <div>simon@harcourtmemorials.com.au</div>
    </div>

    <div class="contact contact--lewis">
      <div class="contact__name">Lewis Harcourt</div>
      <div>Director</div>
      <div>0491630572</div>
      <div>lewis@harcourtmemorials.com.au</div>
    </div>

    <div class="divider"></div>

    <div class="office">
      <div>02 9561 3048</div>
      <div>www.harcourtmemorials.com.au</div>
    </div>
  </section>

  <section class="card card--back">
    <div class="brand-square"></div>
    <div class="wordmark">Harcourt<br>Memorials</div>
    <div class="address">
      <div>Suite 17, 8 Palfrey Lane, West Carlow,</div>
      <div>Sydney NSW 2156</div>
    </div>
  </section>
</body>
</html>
```